Recruitment Agency in Texas, needs a stand out header letter

Our colours are red and grey and can be found on our website
just my logo will be sufficient and address...

Target Market(s)

Engineering Manufacturing

Colors
0094D4
00A9DD
6FCCEA
C7EBF8
E9F6FB
EB3D1F
EC4F4E
F09395
F8D3D4
FCEDEE

Requirements
Must have
• use colors red and grey
Should not have
• Please use same colors and font as my logo. My website is keltrayrecruitment.com

```html
<!DOCTYPE html>
<html lang="en">
<head>
<meta charset="utf-8">
<title>Keltray Recruitment Letterhead</title>
<link rel="stylesheet" href="https://fonts.googleapis.com/css2?family=Arimo:wght@400&display=swap">
<style>
  :root {
    --backdrop: #d9d9d9;
    --paper: #f3f3f3;
    --ink: #3c3c3c;
    --ink-soft: #4a4a4a;
    --brand-grey: #5f6166;
    --brand-red: #e3202b;
    --signature-tone: #d2d2d2;
  }
  * { box-sizing: border-box; margin: 0; padding: 0; }
  html, body {
    width: 1200px; height: 1141px; overflow: hidden;
    background: var(--backdrop);
    font-family: "Arimo", Arial, sans-serif;
  }
  .letterhead {
    position: absolute; left: 333px; top: 87px;
    width: 675px; height: 949px;
    background: var(--paper);
    color: var(--ink);
  }
  .brand {
    position: absolute; top: 64px; left: 0; width: 100%;
    display: flex; justify-content: center; align-items: center; gap: 10px;
  }
  .brand-mark {
    width: 22px; height: 22px;
    background: var(--brand-red);
  }
  .brand-name {
    font-weight: 400; font-size: 32px; line-height: 1;
    color: var(--brand-grey);
  }
  .greeting {
    position: absolute; left: 50px; top: 322px;
    font-size: 17px; color: var(--ink-soft);
  }
  .letter-body {
    position: absolute; left: 50px; top: 373px; width: 575px;
    font-size: 9.4px; line-height: 14.5px; text-align: justify;
  }
  .letter-body p { margin-bottom: 14.5px; }
  .closing {
    position: absolute; left: 50px; top: 690px; font-size: 9.6px;
  }
  .signature {
    position: absolute; left: 46px; top: 720px;
    width: 195px; height: 55px;
    background: linear-gradient(90deg, var(--signature-tone), #e8e8e8);
    border-radius: 4px;
  }
  .contact-footer {
    position: absolute; left: 0; top: 874px; width: 100%;
    text-align: center; font-size: 9.5px; line-height: 12px;
    color: var(--ink-soft);
  }
  .contact-footer .office { margin-top: 3px; }
</style>
</head>
<body>
  <main class="letterhead">
    <header class="brand">
      <span class="brand-mark" aria-hidden="true"></span>
      <span class="brand-name">KeltrayRecruitment</span>
    </header>

    <p class="greeting">Dear Mr. Smith,</p>

    <section class="letter-body">
      <p>Lorem ipsum dolor sit amet, consectetur adipiscing elit. Donec orci purus, luctus vitae dignissim eu, iaculis sed purus. Vivamus faucibus, ipsum nec aliquet viverra, leo mauris condimentum ligula, sit amet sagittis enim ligula quis arcu. Nam egestas tortor id nisi porttitor mattis. In tortor ante, ultricies in suscipit a, tempus non massa. Vivamus et auctor mi. Fusce vel massa nulla. Phasellus nec eros mauris, et scelerisque orci.</p>
      <p>Donec malesuada orci vitae nulla accumsan porta a id massa. Quisque accumsan iaculis magna sit amet fringilla. Maecenas consequat, magna eget tincidunt semper, odio nibh rutrum mi, id feugiat ante nisi eu risus. Vestibulum nunc orci, rhoncus a placerat in, ultricies in mi. Cras mattis varius eros, vel fringilla nisi suscipit eget. Quisque scelerisque sagittis nulla at porttitor.</p>
      <p>Sed id augue vitae urna euismod commodo aliquet a quam. Pellentesque arcu velit, cursus et malesuada ut, consequat et diam. Nullam erat sem, rhoncus id ullamcorper vitae, rhoncus et arcu. In ultricies ultricies nulla, ut rutrum nisi iaculis at. Donec eu magna a metus ornare faucibus. Fusce aliquet faucibus ultricies. Morbi semper, est id tincidunt gravida, sem arcu adipiscing lacus, ac bibendum nulla leo eu purus. Quisque nec diam sed risus consectetur a ccumsan quis quis nibh. Vestibulum id purus lorem.</p>
      <p>It is a long established fact that a reader will be distracted by the readable content of a page when looking at its layout. The point of using Lorem Ipsum is that it has a more-or-less normal distribution of letters, as opposed to using 'Content here, content here', making it look like readable English. Many desktop publishing packages</p>
      <p>ada ut, consequat et diam. Nullam erat sem, rhoncus id ullamcorper vitae, rhoncus et arcu. In ultricies ultricies nulla, ut rutrum nisi iaculis at. Donec eu magna a metus ornare faucibus. Fusce aliquet faucibus ultricies. Morbi semper,</p>
    </section>

    <p class="closing">Sincerely,</p>
    <div class="signature" role="img" aria-label="Handwritten signature of the sender"></div>

    <footer class="contact-footer">
      <div>P: (+1) 555-014-2290&nbsp;&nbsp;F: 555-014-2291</div>
      <div>E: info@keltrayrecruitment.com&nbsp;&nbsp;&nbsp;W: www.keltrayrecruitment.com</div>
      <div class="office">Houston Office, 48 Meridian Park Houston,</div>
    </footer>
  </main>
</body>
</html>
```